Maskottchen für Supplements und laborbasierte Tests im Bereich Longevity
Zielgruppe
Supplements und laborbasierte Tests im Bereich Longevity
Aufgabenstellung
Bitte an den Farben vom angehängten Logo orientieren für das Maskottchen, gerne ein Tier nehmen das für Langlebigkeit steht . Gern sehr kreativ oder auch futuristisch

```html
<!DOCTYPE html>
<html lang="de">
<head>
<meta charset="utf-8">
<title>Regeneration pur – Maskottchen</title>
<link rel="stylesheet" href="https://fonts.googleapis.com/css2?family=Montserrat:ital,wght@0,400;0,500;0,700;0,800;1,700&display=swap">
<style>
  :root {
    --teal-dark: #0c4a4f;
    --green: #9cbf1e;
    --text: #1f2426;
    --mint: #c9f3e4;
    --aqua: #3fd9c4;
    --bg: #ffffff;
  }
  html, body {
    margin: 0;
    padding: 0;
    overflow: hidden;
    background: var(--bg);
  }
  .canvas {
    position: relative;
    width: 1200px;
    height: 674px;
    overflow: hidden;
    background: var(--bg);
    font-family: "Montserrat", Arial, sans-serif;
    color: var(--text);
  }
  .brand {
    position: absolute;
    top: 44px;
    right: 34px;
    display: flex;
    align-items: center;
    gap: 8px;
    font-weight: 700;
    font-size: 26px;
    color: var(--teal-dark);
    letter-spacing: -0.3px;
  }
  .brand-dot {
    width: 14px;
    height: 14px;
    border-radius: 50%;
    background: var(--green);
  }
  .headline {
    position: absolute;
    left: 118px;
    top: 108px;
    margin: 0;
    display: flex;
    align-items: center;
    gap: 12px;
    font-weight: 800;
    font-size: 42px;
    color: var(--teal-dark);
    letter-spacing: -0.5px;
  }
  .headline-pill {
    display: inline-block;
    background: var(--green);
    color: #fff;
    border-radius: 16px;
    padding: 0 14px 4px;
    line-height: 46px;
  }
  .subhead {
    position: absolute;
    left: 118px;
    top: 179px;
    margin: 0;
    font-weight: 700;
    font-size: 22px;
    color: var(--green);
  }
  .body-copy {
    position: absolute;
    left: 118px;
    top: 219px;
    width: 440px;
    margin: 0;
    font-size: 13px;
    font-weight: 500;
    line-height: 26.3px;
    hyphens: auto;
  }
  .quote {
    position: absolute;
    left: 118px;
    top: 455px;
    margin: 0;
    padding-left: 31px;
    width: 300px;
    font-size: 13px;
    font-weight: 700;
    font-style: italic;
    line-height: 26.3px;
  }
  .quote::before {
    content: "";
    position: absolute;
    left: 0;
    top: 1px;
    width: 5px;
    height: 70px;
    background: linear-gradient(to bottom, var(--green), var(--teal-dark));
  }
  .mascot {
    position: absolute;
    left: 612px;
    top: 180px;
    width: 416px;
    height: 404px;
    border-radius: 48% 52% 46% 54% / 50% 44% 56% 50%;
    background: radial-gradient(circle at 45% 45%, var(--mint) 0%, var(--aqua) 60%, var(--teal-dark) 100%);
    opacity: 0.9;
  }
</style>
</head>
<body>
  <main class="canvas">
    <div class="brand"><span class="brand-dot"></span>Lumavita</div>

    <h1 class="headline">Regeneration <span class="headline-pill">pur</span></h1>
    <h2 class="subhead">Symbol für Erneuerung</h2>

    <p class="body-copy">Der Axolotl verkörpert auf einzigartige Weise Regeneration und Vitalität – perfekte Leitmotive für Longevity und moderne Gesundheitsprävention. Als Tier mit außergewöhnlicher Fähigkeit zur Selbstheilung steht er für Zukunft, Aufbruch und biotechnologische Möglichkeiten. Im futuristisch-biologischen Stil wird er zu einem starken, sympathischen Markenbotschafter, der Wissenschaft und Hoffnung verbindet.</p>

    <p class="quote">Wo Erneuerung möglich ist, beginnt ein Weg zu mehr Vitalität, Wachstum und innerer Stärke.</p>

    <div class="mascot" role="img" aria-label="Futuristisches Axolotl-Maskottchen in Mint- und Türkistönen mit DNA-Helix auf dem Körper"></div>
  </main>
</body>
</html>
```